BrindleStaffing Business Card Design

We are a staffing company finding positions for dedicated nurses and physicians.

Target Market(s)

Business Professionals

Industry/Entity Type

Staffing

Contact Information for Business Card

Gordon Pratley
Chairman
417 39th Avenue South
SAINT PETERSBURG FL 33712
813-555-4172 Mobile
813-555-8036 Fax
gpratley@brindlestaffing.com
www.brindlestaffing.com

Font styles to use
Sans Serif

Colors
fbee3e
f04a50
f37122

Requirements
Must have
• Logo Attached, see colors below. We'd like to see Yellow, Orange and Red.

```html
<!DOCTYPE html>
<html lang="en">
<head>
<meta charset="utf-8">
<title>BrindleStaffing Business Card</title>
<link rel="stylesheet" href="https://fonts.googleapis.com/css2?family=Source+Sans+3:wght@400;600;700&display=swap">
<style>
  :root {
    --stage: #9a9b9f;
    --stage-light: #b9babd;
    --card-white: #ffffff;
    --brand-red: #f04a50;
    --brand-orange: #f37122;
    --brand-yellow: #fbee3e;
    --text-white: #ffffff;
  }
  * { margin: 0; padding: 0; box-sizing: border-box; }
  html, body { width: 1200px; height: 1180px; overflow: hidden; }
  body {
    position: relative;
    font-family: "Source Sans 3", "Myriad Pro", sans-serif;
    background: radial-gradient(ellipse at 50% 48%, var(--stage-light) 0%, var(--stage) 60%, #7f8084 100%);
  }
  .card {
    position: absolute;
    width: 714px;
    height: 408px;
    border-radius: 38px;
    overflow: hidden;
  }
  .card-front { left: 117px; top: 136px; background: var(--brand-orange); }
  .card-back { left: 404px; top: 620px; background: var(--brand-orange); }

  .front-top {
    position: absolute; left: 0; top: 0; width: 100%; height: 209px;
    background: var(--card-white);
  }
  .front-logo {
    position: absolute; left: 0; right: 0; top: 72px;
    display: flex; justify-content: center; align-items: center; gap: 14px;
    font-weight: 700; font-size: 60px; letter-spacing: -1px;
    color: var(--brand-red);
    line-height: 1;
  }
  .logo-dot {
    width: 22px; height: 22px; border-radius: 50%;
    background: var(--brand-yellow);
    flex: none;
  }
  .band-right {
    position: absolute; left: 360px; top: 209px; right: 0; height: 40px;
    background: var(--brand-red);
  }
  .band-name {
    position: absolute; left: 0; top: 209px; width: 373px; height: 86px;
    background: var(--brand-red);
    border-bottom: 2px solid var(--card-white);
  }
  .person-name {
    position: absolute; left: 0; width: 308px; top: 214px;
    text-align: center; color: var(--text-white);
    font-weight: 700; font-size: 31px; line-height: 1.1;
  }
  .person-title {
    position: absolute; left: 0; width: 308px; top: 252px;
    text-align: center; color: var(--text-white);
    font-weight: 400; font-size: 28px; line-height: 1.1;
  }
  .portrait {
    position: absolute; left: 314px; top: 199px;
    width: 98px; height: 98px; border-radius: 50%;
    background: var(--brand-yellow);
    border: 3px solid var(--card-white);
  }
  .contact {
    position: absolute; color: var(--text-white);
    font-size: 18px; line-height: 1;
    display: flex; align-items: center; gap: 8px;
    white-space: nowrap;
  }
  .contact svg { width: 17px; height: 17px; flex: none; }
  .address { left: 29px; top: 329px; align-items: flex-start; font-size: 19px; }
  .address-lines { line-height: 27px; margin-top: -4px; }
  .mobile { left: 400px; top: 302px; }
  .fax { left: 400px; top: 328px; }
  .email { left: 400px; top: 354px; }
  .web { left: 400px; top: 380px; }

  .back-logo {
    position: absolute; left: 0; right: 0; top: 140px;
    text-align: center;
    font-weight: 700; font-size: 66px; letter-spacing: -1px;
    color: var(--text-white); line-height: 1;
  }
  .back-url {
    position: absolute; left: 0; right: 0; top: 256px;
    text-align: center; color: var(--text-white);
    font-size: 23px; letter-spacing: 2.5px; font-weight: 400;
  }
  .back-url strong { font-weight: 700; }
</style>
</head>
<body>
  <section class="card card-front" aria-label="Business card front">
    <div class="front-top"></div>
    <div class="front-logo"><span class="logo-dot"></span><span>BrindleStaffing</span></div>
    <div class="band-right"></div>
    <div class="band-name"></div>
    <div class="person-name">Gordon Pratley</div>
    <div class="person-title">Chairman</div>
    <div class="portrait" role="img" aria-label="Portrait photo placeholder"></div>

    <div class="contact address">
      <svg viewBox="0 0 20 20" aria-hidden="true"><path d="M10 1.5a6 6 0 0 0-6 6c0 4.5 6 11 6 11s6-6.5 6-11a6 6 0 0 0-6-6z" fill="none" stroke="#fff" stroke-width="1.8"/><circle cx="10" cy="7.5" r="2.2" fill="none" stroke="#fff" stroke-width="1.8"/></svg>
      <div class="address-lines">417 39th Avenue South<br>Saint Petersburg FL 33712</div>
    </div>
    <div class="contact mobile">
      <svg viewBox="0 0 20 20" aria-hidden="true"><circle cx="10" cy="10" r="8.5" fill="none" stroke="#fff" stroke-width="1.5"/><path d="M7 5.5l1.6 2.4-1 1.2c.6 1.3 1.6 2.3 2.9 2.9l1.2-1 2.4 1.6-.8 1.6c-3.7-.4-6.5-3.2-6.9-6.9z" fill="#fff"/></svg>
      <span>813-555-4172 Mobile</span>
    </div>
    <div class="contact fax">
      <svg viewBox="0 0 20 20" aria-hidden="true"><rect x="5" y="2" width="10" height="6" fill="none" stroke="#fff" stroke-width="1.5"/><rect x="2" y="8" width="16" height="7" rx="1.5" fill="#fff"/><rect x="5" y="13" width="10" height="5" fill="#fff" stroke="#f37122" stroke-width="1"/></svg>
      <span>813-555-8036 Fax</span>
    </div>
    <div class="contact email">
      <svg viewBox="0 0 20 20" aria-hidden="true"><path d="M2 8l8-5 8 5v9H2z" fill="#fff"/><path d="M2 8l8 5 8-5" fill="none" stroke="#f37122" stroke-width="1.5"/></svg>
      <span>gpratley@brindlestaffing.com</span>
    </div>
    <div class="contact web">
      <svg viewBox="0 0 20 20" aria-hidden="true" fill="none" stroke="#fff" stroke-width="1.4"><circle cx="10" cy="10" r="8"/><ellipse cx="10" cy="10" rx="3.5" ry="8"/><path d="M2 10h16M3.5 6h13M3.5 14h13"/></svg>
      <span>www.brindlestaffing.com</span>
    </div>
  </section>

  <section class="card card-back" aria-label="Business card back">
    <div class="back-logo">BrindleStaffing</div>
    <div class="back-url">www.<strong>brindlestaffing</strong>.com</div>
  </section>
</body>
</html>
```